Web Developer Needs a Business Card Design

I need a personal business card design that represents me as a web developer for potential employers. I would like the background to be a dark color on the front for contrast with my logo and name. The back will have all my information along with a smaller version of the logo. I want something with a modern look and feel, not too conservative. This will be used for potential employers and freelance work.

Industry/Entity Type

Business

Contact Information for Business Card

Front should have my logo and name. The back should have all my personal information which would include: name: Tom Varulek, phone: 570-614-3098, email: tomvarulek@quillbox.net, website url: www.tomvarulek.net, logo, web developer.

Font styles to use
Sans Serif

Requirements
Must have
• Must include my logo. The color palette base color will be the logo color.

```html
<!DOCTYPE html>
<html lang="en">
<head>
<meta charset="utf-8">
<title>Tom Varulek – Business Card</title>
<link rel="stylesheet" href="https://fonts.googleapis.com/css2?family=Source+Sans+3:wght@400;600;700&display=swap">
<style>
  :root {
    --stage: #101010;
    --card: #ffffff;
    --brand: #6ecab4;
    --ink: #555555;
    --radius: 10px;
  }
  * { box-sizing: border-box; margin: 0; padding: 0; }
  html, body {
    width: 1200px;
    height: 900px;
    overflow: hidden;
    background: var(--stage);
    font-family: "Source Sans 3", sans-serif;
  }
  .canvas { position: relative; width: 1200px; height: 900px; }
  .card {
    position: absolute;
    top: 306px;
    height: 271px;
    background: var(--card);
    border-radius: var(--radius);
  }
  .card--back { left: 149px; width: 439px; }
  .card--front { left: 608px; width: 441px; height: 272px; }

  .mark {
    position: absolute;
    display: flex;
    align-items: center;
    gap: 9px;
    transform: translate(-50%, -50%);
    color: var(--brand);
    font-weight: 700;
    font-size: 26px;
    white-space: nowrap;
  }
  .mark__dot {
    width: 26px; height: 26px;
    border-radius: 50%;
    background: var(--brand);
    flex: none;
  }
  .card--back .mark { left: 123px; top: 135px; }
  .card--front .mark { left: 129px; top: 136px; }

  .identity { position: absolute; }
  .identity__name { color: var(--brand); font-weight: 700; line-height: 1; }
  .identity__role { color: var(--ink); font-weight: 400; line-height: 1; }

  .card--back .identity { left: 231px; top: 88px; }
  .card--back .identity__name { font-size: 15px; }
  .card--back .identity__role { font-size: 13px; margin-top: 4px; }

  .card--front .identity { left: 243px; top: 115px; }
  .card--front .identity__name { font-size: 19px; }
  .card--front .identity__role { font-size: 16px; margin-top: 6px; }

  .contacts {
    position: absolute;
    left: 232px; top: 137px;
    list-style: none;
    color: var(--ink);
    font-size: 12.5px;
    line-height: 16px;
  }
  .contacts li { display: flex; align-items: center; gap: 6px; }
  .contacts svg { width: 9px; height: 9px; fill: var(--brand); flex: none; }
</style>
</head>
<body>
<main class="canvas">
  <section class="card card--back" aria-label="Card back">
    <div class="mark"><span class="mark__dot"></span>Varulek</div>
    <div class="identity">
      <p class="identity__name">Tom Varulek</p>
      <p class="identity__role">Front-End Developer</p>
    </div>
    <ul class="contacts">
      <li>
        <svg viewBox="0 0 10 10" aria-hidden="true"><path d="M2 0.5l2 2-1 1.2c.6 1.3 1.6 2.3 2.9 2.9L7 5.5l2.5 2-1 2C4.5 9.5.5 5.5.5 1.5z"/></svg>
        570-614-3098
      </li>
      <li>
        <svg viewBox="0 0 10 10" aria-hidden="true"><path d="M0.5 2h9v6h-9z"/><path d="M0.5 2L5 5.5 9.5 2" stroke="#fff" stroke-width="1" fill="none"/></svg>
        tomvarulek@quillbox.net
      </li>
      <li>
        <svg viewBox="0 0 10 10" aria-hidden="true"><circle cx="5" cy="5" r="4.5"/><path d="M0.5 5h9M5 .5c-2 2.5-2 6.5 0 9M5 .5c2 2.5 2 6.5 0 9" stroke="#fff" stroke-width=".8" fill="none"/></svg>
        www.tomvarulek.net
      </li>
    </ul>
  </section>

  <section class="card card--front" aria-label="Card front">
    <div class="mark"><span class="mark__dot"></span>Varulek</div>
    <div class="identity">
      <p class="identity__name">Tom Varulek</p>
      <p class="identity__role">Front-End Developer</p>
    </div>
  </section>
</main>
</body>
</html>
```